TA BRAMLEY BUSINESS CARD DESIGN PROJECT

We need to utilize our logo that was expertly created on PixelHarbor and now need to match this with a business card design.

```html
<!DOCTYPE html>
<html lang="en">
<head>
<meta charset="utf-8">
<title>TA BRAMLEY Business Cards</title>
<link rel="stylesheet" href="https://fonts.googleapis.com/css2?family=Montserrat:wght@400;500;700&display=swap">
<style>
  :root {
    --page-bg: #3a3a3a;
    --card-white: #ffffff;
    --card-dark: #2a2a2a;
    --brand-blue: #0a57b8;
    --brand-light: #4a9df0;
    --ink: #1c1c1c;
  }
  * { box-sizing: border-box; margin: 0; padding: 0; }
  html, body { width: 1200px; height: 1200px; overflow: hidden; }
  body {
    background: var(--page-bg);
    font-family: "Montserrat", sans-serif;
    display: flex;
    flex-direction: column;
    align-items: center;
    justify-content: center;
    gap: 60px;
  }
  .card {
    position: relative;
    width: 860px;
    height: 490px;
    border-radius: 40px;
    border-bottom: 5px solid var(--brand-blue);
    box-shadow: 0 14px 30px rgba(0,0,0,0.45);
    overflow: hidden;
  }
  .card--front { background: var(--card-white); }
  .card--back { background: var(--card-dark); }

  .brand {
    position: absolute;
    display: flex;
    align-items: center;
    gap: 16px;
    font-weight: 700;
    white-space: nowrap;
  }
  .brand__mark { flex: none; }
  .card--front .brand {
    top: 150px;
    right: 60px;
    font-size: 38px;
    letter-spacing: 4px;
    color: var(--brand-blue);
  }
  .card--front .brand__mark { width: 30px; height: 30px; background: var(--brand-blue); }
  .card--back .brand {
    top: 50%; left: 50%;
    transform: translate(-50%, -50%);
    font-size: 58px;
    letter-spacing: 5px;
    color: var(--brand-light);
  }
  .card--back .brand__mark { width: 42px; height: 42px; background: var(--brand-light); }

  .contact {
    position: absolute;
    left: 56px;
    bottom: 64px;
    color: var(--ink);
  }
  .contact__name {
    font-size: 36px;
    font-weight: 700;
    color: var(--brand-blue);
    line-height: 1;
  }
  .contact__role {
    font-size: 22px;
    font-weight: 500;
    letter-spacing: 1px;
    margin: 6px 0 18px;
  }
  .contact__list { list-style: none; }
  .contact__item {
    display: flex;
    align-items: flex-start;
    gap: 14px;
    font-size: 19px;
    line-height: 1.3;
    margin-bottom: 6px;
  }
  .contact__icon { width: 22px; height: 22px; flex: none; margin-top: 2px; fill: var(--brand-blue); }
</style>
</head>
<body>
  <section class="card card--front" aria-label="Business card front">
    <div class="brand"><span class="brand__mark"></span>TA BRAMLEY</div>
    <div class="contact">
      <p class="contact__name">FULL NAME</p>
      <p class="contact__role">POSITION</p>
      <ul class="contact__list">
        <li class="contact__item">
          <svg class="contact__icon" viewBox="0 0 24 24"><path d="M6.6 10.8a15.1 15.1 0 0 0 6.6 6.6l2.2-2.2a1 1 0 0 1 1-.25 11.4 11.4 0 0 0 3.6.57 1 1 0 0 1 1 1V20a1 1 0 0 1-1 1A17 17 0 0 1 3 4a1 1 0 0 1 1-1h3.5a1 1 0 0 1 1 1c0 1.25.2 2.45.57 3.57a1 1 0 0 1-.25 1z"/></svg>
          (000) 000 0000
        </li>
        <li class="contact__item">
          <svg class="contact__icon" viewBox="0 0 24 24"><path d="M2 5h20v14H2z M4 7v.5l8 5 8-5V7l-8 5z" fill-rule="evenodd"/></svg>
          email@company.com
        </li>
        <li class="contact__item">
          <svg class="contact__icon" viewBox="0 0 24 24"><circle cx="12" cy="12" r="9" fill="none" stroke="#0a57b8" stroke-width="2"/><ellipse cx="12" cy="12" rx="4" ry="9" fill="none" stroke="#0a57b8" stroke-width="1.5"/><path d="M3 12h18M5 7.5h14M5 16.5h14" stroke="#0a57b8" stroke-width="1.5"/></svg>
          www.company.com
        </li>
        <li class="contact__item">
          <svg class="contact__icon" viewBox="0 0 24 24"><path d="M12 2a7 7 0 0 0-7 7c0 5 7 13 7 13s7-8 7-13a7 7 0 0 0-7-7zm0 9.5A2.5 2.5 0 1 1 12 6.5a2.5 2.5 0 0 1 0 5z"/></svg>
          <span>123 Name Street, 000<br>Your City, 00000-000</span>
        </li>
      </ul>
    </div>
  </section>

  <section class="card card--back" aria-label="Business card back">
    <div class="brand"><span class="brand__mark"></span>TA BRAMLEY</div>
  </section>
</body>
</html>
```